Psychotherapy, Life Coaching, Writer, Motivational Speaker

I am a psychotherapist, life coach, writer and speaker on health and wellness issues. I am a humanist - who believes that we are born to self-actualize - but life - changes that course. That we develop armor and coping mechanisms that divert our growth. I help people examine their road blocks to happiness. My business is unique in that I do concierge therapy. I work intensively - with multi-day sessions, I work internationally through tele-therapy - and traditionally - in an office space. My work is tailored to your needs.

Target Market(s)

Broad

Industry/Entity Type

Health

Contact Information for Business Card

Listen And Grow
Sam Perriton
248 East 39th Street
New York, NY 10027
(305) 555-0173

Requirements
Must have
• Clean lines... not too busy...
• FB page listing: Listen And Grow
• my Web page: www.listenandgrow-example.com
Nice to have
• I would love to be able to list the services: Psychotherapist, Life Coach, Motivational Speaker and Writer - but also don't want a crazy crowded card. Feel free to use the back for description.
Should not have
• Stay away from corny imagery - lotus flowers, zen, lily pond, clouds.

```html
<!DOCTYPE html>
<html lang="en">
<head>
<meta charset="utf-8">
<title>Listen And Grow – Business Card</title>
<link rel="stylesheet" href="https://fonts.googleapis.com/css2?family=Lato:wght@400;700&display=swap">
<style>
  :root {
    --backdrop: #e6e7e9;
    --card: #fbfbfb;
    --brand-blue: #4d7cb9;
    --band-blue: #3f6fb0;
    --band-blue-light: #5e8cc7;
    --ink: #1f1f24;
  }
  * { margin: 0; padding: 0; box-sizing: border-box; }
  html, body { width: 1200px; height: 720px; overflow: hidden; }
  body {
    background: var(--backdrop);
    font-family: "Lato", Arial, sans-serif;
    color: var(--ink);
    position: relative;
  }
  .card {
    position: absolute;
    top: 241px;
    width: 419px;
    height: 239px;
    background: var(--card);
    overflow: hidden;
  }
  .card-front { left: 148px; }
  .card-back { left: 633px; }

  .front-title {
    position: absolute;
    right: 11px;
    top: 17px;
    font-size: 23px;
    font-weight: 700;
    color: var(--brand-blue);
    white-space: nowrap;
  }
  .front-accent {
    position: absolute;
    left: 0;
    top: 95px;
    width: 15px;
    height: 139px;
    background: linear-gradient(180deg, var(--band-blue-light), var(--band-blue));
  }
  .contact-block {
    position: absolute;
    left: 31px;
    top: 93px;
  }
  .person-name {
    font-size: 16.5px;
    font-weight: 700;
    color: var(--brand-blue);
    line-height: 20px;
  }
  .person-credentials {
    font-size: 13px;
    font-weight: 400;
    color: var(--ink);
  }
  .person-role {
    font-size: 13px;
    line-height: 17px;
    margin-bottom: 2px;
  }
  .contact-list { list-style: none; }
  .contact-item {
    display: flex;
    align-items: center;
    gap: 4px;
    font-size: 13px;
    line-height: 16px;
    white-space: nowrap;
  }
  .contact-icon { width: 11px; height: 11px; flex: none; }
  .social-square {
    width: 10px; height: 10px;
    background: var(--band-blue);
    border-radius: 1.5px;
    flex: none;
    margin-right: 1px;
  }
  .postal-address {
    font-style: normal;
    font-size: 11.5px;
    line-height: 14.5px;
    margin-top: 7px;
  }

  .back-title {
    position: absolute;
    left: 31px;
    top: 57px;
    font-size: 20px;
    font-weight: 700;
    color: var(--brand-blue);
    white-space: nowrap;
  }
  .service-list {
    position: absolute;
    left: 31px;
    top: 97px;
    list-style: none;
    font-size: 13px;
    line-height: 16px;
  }
  .appointment-line {
    position: absolute;
    left: 33px;
    top: 164px;
    font-size: 13px;
    white-space: nowrap;
  }
  .back-band {
    position: absolute;
    left: 0;
    bottom: 0;
    width: 100%;
    height: 17px;
    background: linear-gradient(90deg, var(--band-blue-light), var(--band-blue));
  }
</style>
</head>
<body>
  <section class="card card-front" aria-label="Business card front">
    <h1 class="front-title">Listen And Grow</h1>
    <div class="front-accent"></div>
    <div class="contact-block">
      <p class="person-name">Sam Perriton,<span class="person-credentials"> LMHC, NCC</span></p>
      <p class="person-role">Psychotherapist.</p>
      <ul class="contact-list">
        <li class="contact-item">
          <svg class="contact-icon" viewBox="0 0 12 12" aria-hidden="true"><path fill="#3f6fb0" d="M1 4.5c0-1.6 2.2-2.5 5-2.5s5 .9 5 2.5v.8H8.6v-1c-.7-.4-1.6-.5-2.6-.5s-1.9.1-2.6.5v1H1zM3 6h6l1.5 4.5h-9z"/></svg>
          <span>(305) 555-0173</span>
        </li>
        <li class="contact-item">
          <svg class="contact-icon" viewBox="0 0 12 12" aria-hidden="true"><rect x="1" y="2.5" width="10" height="7" fill="#3f6fb0"/><path d="M1.5 3l4.5 3.5L10.5 3" fill="none" stroke="#fff" stroke-width="1"/></svg>
          <span>sperritonmail@example.com</span>
        </li>
        <li class="contact-item">
          <svg class="contact-icon" viewBox="0 0 12 12" aria-hidden="true"><g fill="none" stroke="#3f6fb0" stroke-width="1"><circle cx="6" cy="6" r="4.8"/><ellipse cx="6" cy="6" rx="2" ry="4.8"/><path d="M1.2 6h9.6M2 3.5h8M2 8.5h8"/></g></svg>
          <span>www.listenandgrow-example.com</span>
        </li>
        <li class="contact-item">
          <span class="social-square" aria-hidden="true"></span>
          <span>Listen And Grow</span>
        </li>
      </ul>
      <address class="postal-address">248 East 39th Street<br>New York, NY 10027</address>
    </div>
  </section>

  <section class="card card-back" aria-label="Business card back">
    <h2 class="back-title">Listen and Grow</h2>
    <ul class="service-list">
      <li>Psychotherapy,</li>
      <li>Coaching,</li>
      <li>Wellness Media</li>
    </ul>
    <p class="appointment-line">Your Next Appoinment is at...................... at.............. am/pm</p>
    <div class="back-band"></div>
  </section>
</body>
</html>
```